Velvet Glow Co. Derma Roller packaging design

I need a box designed for a skin care brand called Velvet Glow Co. The box will be for our Derma Roller- a skin rejuvenation device. It will be sold online with lots of competition. I would like a modern, high end design, something that stands out and looks amazing. My logo is blush pink and black, for packaging i need no more than 3 colours, maybe gold if any other colour is used. A photo of a sample derma roller is attached below for an idea of what the product looks like, however my roller with have a clear handle with a black roller. The roller comes in a clear case, the box dimensions will need to be 16 cm long, 4 cm high, 4.5 cm wide.
ATTACHED ARE 2 SAMPLE BOXES AS AN EXAMPLE OF THE SIZE OF BOX REQUIRED!

Target Market(s)

25-50 year old women in the US

Colors
e667a6
000000
efefef

Requirements
Must have
• LOGO
• NAME OF PRODUCT- Cosmetic Derma Roller
• NEEDLE DEPTH- 0.25mm
• CAUTION- For personal use only, Do not use if allergic to metal, Do not use on open skin, wounds or active acne, sterilise roller before and after use.
Nice to have
• BENEFITS- Skin Rejuvenation, Collagen Induction Therapy, Increase product absorption, reduce acne scars and pigmentation
• FEATURES- 540 high quality titanium needles, ultra sharp needle tips, cross-line needle arrangement, ergonomic handle, anti slip grip,

```html
<!DOCTYPE html>
<html lang="en">
<head>
<meta charset="utf-8">
<title>Velvet Glow Co. — Cosmetic Derma Roller Packaging</title>
<link href="https://fonts.googleapis.com/css2?family=Oswald:wght@400;500&display=swap" rel="stylesheet">
<style>
  :root {
    --canvas-bg: #fbf5f4;
    --panel-pink: #f4d2cb;
    --floral-mauve: #b98f8a;
    --floral-light: #e9bfb6;
    --label-white: #ffffff;
    --rose-gold: #d29c86;
    --rose-gold-light: #f0cdbd;
    --ink: #1d1a1a;
  }
  * { margin: 0; padding: 0; box-sizing: border-box; }
  html, body { width: 1200px; height: 1200px; overflow: hidden; }
  body {
    background: var(--canvas-bg);
    position: relative;
    font-family: "Oswald", "Arial Narrow", sans-serif;
  }
  .box-face {
    position: absolute;
    top: 62px;
    width: 400px;
    height: 1076px;
    background: var(--panel-pink);
    box-shadow: 0 4px 14px rgba(120, 80, 75, 0.25);
    overflow: hidden;
  }
  .box-face--front { left: 134px; }
  .box-face--back { left: 666px; }
  .floral-artwork {
    position: absolute;
    inset: 0;
    background:
      radial-gradient(ellipse 70% 30% at 50% 18%, var(--floral-mauve) 0%, transparent 75%),
      radial-gradient(ellipse 70% 28% at 50% 82%, var(--floral-mauve) 0%, transparent 75%),
      radial-gradient(ellipse 60% 20% at 50% 40%, var(--floral-light) 0%, transparent 80%),
      linear-gradient(180deg, #c9a19b 0%, var(--panel-pink) 50%, #c9a19b 100%);
    opacity: 0.85;
  }
  .label {
    position: absolute;
    background: var(--label-white);
    border: 8px solid var(--rose-gold);
    border-image: linear-gradient(135deg, var(--rose-gold-light), var(--rose-gold), var(--rose-gold-light), var(--rose-gold)) 1;
  }
  .box-face--front .label { left: 24px; top: 360px; width: 354px; height: 356px; }
  .box-face--back .label { left: 24px; top: 360px; width: 355px; height: 359px; }
  .brand-name {
    position: absolute;
    left: 0; right: 0; top: 118px;
    text-align: center;
    font-size: 30px;
    font-weight: 400;
    letter-spacing: 2px;
    color: var(--ink);
    text-transform: uppercase;
  }
  .product-title {
    color: var(--rose-gold);
    font-weight: 400;
    font-size: 23px;
    letter-spacing: 0.5px;
    text-transform: uppercase;
    text-align: center;
  }
  .box-face--front .product-title { position: absolute; left: 0; right: 0; top: 262px; }
  .box-face--back .product-title { margin-top: 40px; }
  .spec-list {
    margin: 26px 0 0 28px;
    width: 310px;
    font-size: 11.6px;
    line-height: 19.3px;
    font-weight: 500;
    color: var(--ink);
    text-transform: uppercase;
    letter-spacing: 0.1px;
  }
  .spec-list p + p { margin-top: 19px; }
</style>
</head>
<body>
  <section class="box-face box-face--front">
    <div class="floral-artwork" role="img" aria-label="Engraved floral pattern of mauve leaves, blossoms and berries"></div>
    <div class="label">
      <div class="brand-name">Velvet Glow Co.</div>
      <h1 class="product-title">Cosmetic Derma Roller</h1>
    </div>
  </section>

  <section class="box-face box-face--back">
    <div class="floral-artwork" role="img" aria-label="Engraved floral pattern of mauve leaves, blossoms and berries"></div>
    <div class="label">
      <h2 class="product-title">Cosmetic Derma Roller</h2>
      <div class="spec-list">
        <p>Benefits: skin rejuvenation, collagen induction therapy, increase product absorption, reduce acne scars and pigmentation</p>
        <p>Features: 540 high quality 0.25 mm titanium needles, ultra sharp needle tips, cross-line needle arrangement, ergonomic handle, anti slip grip</p>
        <p>Caution: for personal use only, do not use if allergic to metal, do not use on open skin, wounds or active acne, sterilise roller before and after use.</p>
      </div>
    </div>
  </section>
</body>
</html>
```